OBK Farcoast Logistics Limited

We need the buissnes card to be very exclusive. As we are all young in our company. We need this to be the gate to make our clients feel deep interest for us.

We are focused in as International Trade advisors, and our products go from Oil Tanker Ships to Rubber balls for dogs.

Our Slogan is Bringing Far Near.
And our main marketing will be through Internet.

We were stablished in 2009 In Mexico and we also have offices in Hong Kong.
We have representatives in China and Europe.

Target Market(s)

Is every company or Individual that wants to develop an International Project or product development or Logistic service of Goods and people.
Some of our current projects are Ship Brokerage, Mine Brokerage, Real State and Product Pormotional development.

Industry/Entity Type

It Company

Requirements
Must have
• Our Logo and slogan, and make the card accoriding to the logo.
Nice to have
• Our Colors

```html
<!DOCTYPE html>
<html lang="en">
<head>
<meta charset="utf-8">
<title>OBK Farcoast Logistics Limited – Business Card</title>
<link rel="stylesheet" href="https://fonts.googleapis.com/css2?family=Source+Sans+3:wght@400;600;700&display=swap">
<style>
  :root {
    --stage: #e9ebee;
    --silver-light: #f4f5f6;
    --silver-mid: #dcdee1;
    --silver-dark: #c9ccd0;
    --brand-blue: #1d80c3;
    --brand-navy: #2c3f94;
    --brand-green: #8cc63f;
    --ink-grey: #5f6469;
    --white: #ffffff;
  }
  * { box-sizing: border-box; margin: 0; padding: 0; }
  html, body {
    width: 1200px; height: 720px; overflow: hidden;
    background: var(--stage);
    font-family: "Source Sans 3", "Helvetica Neue", Arial, sans-serif;
  }
  .stage {
    position: relative; width: 1200px; height: 720px;
    display: flex; align-items: center; justify-content: center; gap: 40px;
  }
  .card {
    position: relative; width: 540px; height: 309px; overflow: hidden;
    border-radius: 4px;
    background: linear-gradient(115deg, var(--silver-dark) 0%, var(--silver-light) 35%, var(--silver-mid) 60%, var(--silver-light) 85%, var(--silver-dark) 100%);
    box-shadow: 0 2px 10px rgba(0,0,0,.15);
  }

  /* Contact side */
  .brand-lockup {
    position: absolute; left: 0; right: 0; top: 18px;
    display: flex; flex-direction: column; align-items: center;
    transform: translateX(-40px);
  }
  .brand-lockup__name {
    display: flex; align-items: center; gap: 8px;
    font-weight: 700; font-size: 40px; line-height: 1; letter-spacing: 2px;
    color: var(--brand-green);
  }
  .brand-lockup__dot {
    width: 16px; height: 16px; border-radius: 50%; background: var(--brand-blue);
  }
  .brand-lockup__slogan {
    margin-top: 4px; font-size: 11px; color: var(--brand-blue); letter-spacing: .3px;
  }
  .contact-band {
    position: absolute; left: 0; right: 0; top: 122px; bottom: 0;
    background: var(--brand-blue);
    padding: 36px 0 0 30px; color: var(--white);
  }
  .contact-band__mark {
    position: absolute; right: 70px; top: 14px;
    font-weight: 700; font-size: 46px; letter-spacing: 2px;
    color: rgba(255,255,255,.14);
  }
  .holder { font-size: 19px; line-height: 1.1; margin-bottom: 8px; }
  .holder__name { font-weight: 700; }
  .holder__role { font-weight: 400; font-size: 16px; }
  .contact-list { list-style: none; font-size: 15px; line-height: 22px; letter-spacing: .5px; }
  .contact-list li { display: flex; align-items: center; gap: 7px; }
  .contact-list .pair { gap: 22px; }
  .contact-list .pair span { display: flex; align-items: center; gap: 7px; }
  .icon { width: 13px; height: 13px; flex: none; }

  /* Brand side */
  .logo-panel {
    position: absolute; left: 50%; top: 48%; transform: translate(-50%, -50%);
    display: flex; align-items: center; gap: 12px;
    font-weight: 700; font-size: 64px; letter-spacing: 3px; color: var(--brand-blue);
  }
  .logo-panel__dot { width: 26px; height: 26px; border-radius: 50%; background: var(--brand-green); }
  .web-address {
    position: absolute; right: 46px; bottom: 28px;
    font-size: 19px; letter-spacing: 2.5px; color: var(--ink-grey);
  }
  .web-address__domain { color: var(--brand-blue); }
</style>
</head>
<body>
<main class="stage">

  <section class="card card--contact" aria-label="Business card, contact side">
    <div class="brand-lockup">
      <div class="brand-lockup__name"><span class="brand-lockup__dot"></span>OBK</div>
      <div class="brand-lockup__slogan">Bringing Far Near</div>
    </div>

    <div class="contact-band">
      <div class="contact-band__mark" aria-hidden="true">OBK</div>
      <p class="holder"><span class="holder__name">Your Name,</span> <span class="holder__role">Position</span></p>
      <ul class="contact-list">
        <li class="pair">
          <span>
            <svg class="icon" viewBox="0 0 16 16" aria-hidden="true"><circle cx="8" cy="8" r="7.5" fill="#fff"/><path d="M5.2 4.2l1.6-.3.8 2-1 .8a6 6 0 0 0 2.7 2.7l.8-1 2 .8-.3 1.6c-3.6.3-6.9-3-6.6-6.6z" fill="var(--brand-blue)"/></svg>
            123-456-7890
          </span>
          <span>
            <svg class="icon" viewBox="0 0 16 16" aria-hidden="true"><rect x="4" y="1" width="8" height="14" rx="1.5" fill="#fff"/><rect x="5.3" y="3" width="5.4" height="7" fill="var(--brand-blue)"/><circle cx="8" cy="12.5" r="1" fill="var(--brand-blue)"/></svg>
            123-456-7890
          </span>
        </li>
        <li>
          <svg class="icon" viewBox="0 0 16 16" aria-hidden="true"><circle cx="8" cy="8" r="7.5" fill="#fff"/><rect x="4" y="5.2" width="8" height="5.6" fill="var(--brand-blue)"/><path d="M4 5.2l4 3 4-3" stroke="#fff" stroke-width="1" fill="none"/></svg>
          info@farcoast.com
        </li>
        <li>
          <svg class="icon" viewBox="0 0 16 16" aria-hidden="true"><circle cx="8" cy="8" r="7.5" fill="#fff"/><circle cx="8" cy="8" r="4.5" fill="none" stroke="var(--brand-blue)" stroke-width="1"/><path d="M3.5 8h9M8 3.5c-2 2.5-2 6.5 0 9M8 3.5c2 2.5 2 6.5 0 9" stroke="var(--brand-blue)" stroke-width="1" fill="none"/></svg>
          www.farcoast.com
        </li>
        <li class="address">00, Complex Name, City, State, 00045</li>
      </ul>
    </div>
  </section>

  <section class="card card--brand" aria-label="Business card, brand side">
    <div class="logo-panel"><span class="logo-panel__dot"></span>OBK</div>
    <p class="web-address">www.<span class="web-address__domain">farcoast</span>.com</p>
  </section>

</main>
</body>
</html>
```